Namecard Designs+Logo for a High End Automobile Company

We need a new business card for our company called Nordel Motorwerk.

www.nordelmotorwerk.example.sg
Our new website will be up in 2.5 months time.

We sell used and brand new continental cars like Valcrest, KTR, Almira, Dunvale and etc. Currently we are operating from 2 offices in Singapore and United Kingdom.

We want a design which is serious. We are open to colours but try to keep it at a maximum of 3 colours.

We prefer something simple and minimal. We are open to 2 sides printing or even 2 sided namecards. Both UK and Singapore company offices address must be in; either side by side, front and back, or even 2 sided cards.

The logo can be a text logo, emblem, abstract, pictorial or combination.

We are printing with Printlyx.com so please kindly follow the printing guideline.

http://uk.printlyx.example/help/faq/templates-and-guidelines.html

Rich and Car Enthusiasts

Printing

• Our 2 offices; UK and Singapore.

Our slogan which is " The Automobile Specialist"
• Not more than 3 colours

```html
<!DOCTYPE html>
<html lang="en">
<head>
<meta charset="utf-8">
<title>Nordel Motorwerk – Business Card and Logo</title>
<link rel="stylesheet" href="https://fonts.googleapis.com/css2?family=Michroma&family=Archivo+Black&display=swap">
<style>
  :root {
    --stage: #3a3a3c;
    --card-blue: #1f86d6;
    --card-white: #ffffff;
    --ink-white: #ffffff;
    --ink-navy: #1d3f86;
    --ink-grey: #3a3a3a;
    --ink-dark: #222222;
    --accent-blue: #1e6fc4;
    --silver: #b9bcc0;
    --silver-dark: #7d8086;
    --back-center: #33b3ea;
    --back-edge: #1f3f9a;
  }
  * { margin: 0; padding: 0; box-sizing: border-box; }
  html, body { width: 1200px; height: 900px; overflow: hidden; }
  body {
    position: relative;
    background: var(--stage);
    font-family: "Michroma", "Arial", sans-serif;
  }
  .card {
    position: absolute;
    border-radius: 22px;
    overflow: hidden;
    box-shadow: 0 8px 18px rgba(0,0,0,0.45);
  }
  .card--front-blue { left: 22px; top: 123px; width: 574px; height: 330px; background: var(--card-blue); color: var(--ink-white); }
  .card--front-white { left: 622px; top: 127px; width: 556px; height: 319px; background: var(--card-white); color: var(--ink-grey); }
  .card--back {
    left: 384px; top: 517px; width: 594px; height: 340px;
    background: radial-gradient(ellipse at 50% 45%, var(--back-center) 0%, var(--card-blue) 40%, var(--back-edge) 100%);
  }

  .holder { position: absolute; text-align: center; }
  .holder__name { font-size: 15px; letter-spacing: 1px; line-height: 1.2; }
  .holder__role { font-size: 10px; letter-spacing: 1px; }
  .card--front-blue .holder { left: 345px; top: 40px; width: 205px; }
  .card--front-white .holder { left: 318px; top: 38px; width: 205px; }
  .card--front-white .holder__name { color: var(--ink-navy); }

  .offices { position: absolute; list-style: none; font-size: 7.4px; letter-spacing: 0.4px; line-height: 1.55; }
  .offices li + li { margin-top: 9px; }
  .offices__label { display: block; font-size: 8.4px; letter-spacing: 1px; }
  .card--front-blue .offices { left: 30px; top: 38px; width: 300px; }
  .card--front-white .offices { left: 30px; top: 36px; width: 280px; color: var(--ink-dark); }
  .card--front-white .offices__label { color: var(--accent-blue); }

  .divider { position: absolute; width: 3px; }
  .card--front-blue .divider { left: 228px; top: 171px; height: 141px; background: var(--ink-white); }
  .card--front-white .divider { left: 218px; top: 168px; height: 132px; background: var(--accent-blue); }

  .slogan { position: absolute; font-size: 11.5px; letter-spacing: 1px; white-space: nowrap; }
  .card--front-blue .slogan { left: 240px; top: 222px; }
  .card--front-white .slogan { left: 232px; top: 218px; color: var(--ink-dark); }

  .contacts { position: absolute; list-style: none; font-size: 8.6px; letter-spacing: 0.6px; }
  .card--front-blue .contacts { left: 252px; top: 243px; }
  .card--front-white .contacts { left: 244px; top: 238px; color: var(--ink-dark); }
  .contacts li { display: flex; align-items: center; height: 15px; white-space: nowrap; }
  .contacts svg { width: 11px; height: 11px; margin-right: 11px; flex: none; }

  .brand { position: absolute; text-align: center; }
  .brand__mark { display: block; margin: 0 auto 12px; border-radius: 50%; background: var(--silver); }
  .brand__name { font-size: 11px; letter-spacing: 0.5px; white-space: nowrap; }
  .card--front-blue .brand { left: 12px; top: 186px; width: 210px; }
  .card--front-blue .brand__mark { width: 74px; height: 74px; }
  .card--front-white .brand { left: 6px; top: 182px; width: 206px; }
  .card--front-white .brand__mark { width: 74px; height: 74px; }
  .card--front-white .brand__name { color: var(--accent-blue); }
  .card--back .brand { left: 0; top: 100px; width: 100%; }
  .card--back .brand__mark { width: 96px; height: 96px; margin-bottom: 18px; }
  .card--back .brand__name { font-size: 24px; color: var(--ink-white); }

  .logo-heading {
    position: absolute; left: 18px; top: 534px;
    font-family: "Archivo Black", "Arial Black", sans-serif;
    font-size: 31px; color: var(--ink-white); letter-spacing: 0.5px;
  }
  .logo-panel { position: absolute; left: 50px; top: 597px; width: 262px; height: 258px; background: var(--card-white); }
  .logo-panel .brand { left: 0; top: 70px; width: 100%; }
  .logo-panel .brand__mark { width: 80px; height: 80px; background: var(--silver-dark); }
  .logo-panel .brand__name { font-size: 14px; color: var(--ink-grey); }
</style>
</head>
<body>

  <section class="card card--front-blue" aria-label="Business card front, blue version">
    <ul class="offices">
      <li><span class="offices__label">SINGAPORE</span>18 Kallang Vale Road, #03-11<br>Singapore 339018</li>
      <li><span class="offices__label">UNITED KINGDOM</span>42 Harrowgate Lane<br>London EC1A 4XX</li>
    </ul>
    <div class="holder">
      <p class="holder__name">MARCUS HALE</p>
      <p class="holder__role">MANAGER</p>
    </div>
    <div class="brand">
      <span class="brand__mark"></span>
      <p class="brand__name">NORDEL MOTORWERK</p>
    </div>
    <div class="divider"></div>
    <p class="slogan">THE AUTOMOBILE SPECIALIST</p>
    <ul class="contacts">
      <li><svg viewBox="0 0 12 12"><path d="M2 1h3l1 3-1.5 1a6 6 0 0 0 2.5 2.5L8 6l3 1v3c-5 1-10-4-9-9z" fill="#fff"/></svg>0410 555 018</li>
      <li><svg viewBox="0 0 12 12"><rect x="0.5" y="2" width="11" height="8" rx="1" fill="#fff"/></svg>marcus@nordelmotorwerk.example.sg</li>
      <li><svg viewBox="0 0 12 12"><circle cx="6" cy="6" r="5" fill="none" stroke="#fff" stroke-width="1.5"/><circle cx="6" cy="6" r="2" fill="#fff"/></svg>www.nordelmotorwerk.example.sg</li>
    </ul>
  </section>

  <section class="card card--front-white" aria-label="Business card front, white version">
    <ul class="offices">
      <li><span class="offices__label">SINGAPORE</span>18 Kallang Vale Road, #03-11<br>Singapore 339018</li>
      <li><span class="offices__label">UNITED KINGDOM</span>42 Harrowgate Lane<br>London EC1A 4XX</li>
    </ul>
    <div class="holder">
      <p class="holder__name">MARCUS HALE</p>
      <p class="holder__role">MANAGER</p>
    </div>
    <div class="brand">
      <span class="brand__mark"></span>
      <p class="brand__name">NORDEL MOTORWERK</p>
    </div>
    <div class="divider"></div>
    <p class="slogan">THE AUTOMOBILE SPECIALIST</p>
    <ul class="contacts">
      <li><svg viewBox="0 0 12 12"><path d="M2 1h3l1 3-1.5 1a6 6 0 0 0 2.5 2.5L8 6l3 1v3c-5 1-10-4-9-9z" fill="#1e6fc4"/></svg>0410 555 018</li>
      <li><svg viewBox="0 0 12 12"><rect x="0.5" y="2" width="11" height="8" rx="1" fill="#1e6fc4"/></svg>marcus@nordelmotorwerk.example.sg</li>
      <li><svg viewBox="0 0 12 12"><circle cx="6" cy="6" r="5" fill="none" stroke="#1e6fc4" stroke-width="1.5"/><circle cx="6" cy="6" r="2" fill="#1e6fc4"/></svg>www.nordelmotorwerk.example.sg</li>
    </ul>
  </section>

  <h2 class="logo-heading">LOGO DESIGNED</h2>

  <section class="logo-panel" aria-label="Logo on white">
    <div class="brand">
      <span class="brand__mark"></span>
      <p class="brand__name">NORDEL MOTORWERK</p>
    </div>
  </section>

  <section class="card card--back" aria-label="Business card back">
    <div class="brand">
      <span class="brand__mark"></span>
      <p class="brand__name">NORDEL MOTORWERK</p>
    </div>
  </section>

</body>
</html>
```